New Web Design Project

Number of Pages Required

1 page

Requirements
Must have
• An Overview / Background of the Business & Services(not for profit rescue animal farm)
• The Target Market / Audience you are trying to reach (animal lovers)
• Design Specifics; any preferences or ideas for Style, Colour, Imagery, etc (no preferences)

```html
<!DOCTYPE html>
<html lang="en">
<head>
<meta charset="utf-8">
<title>We Love Animals</title>
<link rel="stylesheet" href="https://fonts.googleapis.com/css2?family=Courgette&family=Nunito+Sans:wght@400;800&family=Open+Sans:wght@400&display=swap">
<style>
  :root {
    --page-bg: #f2f2f2;
    --ink: #111111;
    --body-text: #6e6e6e;
    --rule: #c9c9c9;
    --icon-grey: #c4c4c4;
    --accent: #f15a5a;
    --band-bg: #7f7780;
    --band-rule: #a59ea6;
    --white: #ffffff;
  }
  * { box-sizing: border-box; margin: 0; padding: 0; }
  html, body { width: 1200px; height: 1000px; overflow: hidden; }
  body { background: var(--page-bg); font-family: "Open Sans", sans-serif; position: relative; }

  .section-title {
    position: absolute; left: 0; width: 1200px; text-align: center;
    font-family: "Courgette", cursive; font-weight: 400; font-size: 58px; line-height: 1;
  }
  .team .section-title { top: 14px; color: var(--ink); }

  .title-rule { position: absolute; height: 1px; }
  .title-mark { position: absolute; width: 22px; height: 18px; border-radius: 50% 50% 45% 45%; }

  .connector { position: absolute; left: 0; top: 300px; }

  .member { position: absolute; top: 180px; width: 400px; text-align: center; }
  .member--left { left: 150px; }
  .member--right { left: 653px; }

  .portrait {
    width: 270px; height: 270px; margin: 0 auto; border-radius: 50%;
    background: var(--white); padding: 9px;
  }
  .portrait-fill { width: 100%; height: 100%; border-radius: 50%; }
  .portrait-fill--man { background: radial-gradient(circle at 60% 45%, #b9b8bc 0%, #8e8a87 45%, #5d6b6e 100%); }
  .portrait-fill--woman { background: radial-gradient(circle at 65% 60%, #d8a866 0%, #c28a55 35%, #9fc8cc 70%, #e8d2c0 100%); }

  .member-name {
    margin-top: 44px; font-family: "Nunito Sans", sans-serif; font-weight: 400;
    font-size: 28px; color: var(--ink); line-height: 1.2;
  }
  .member-name strong { font-weight: 800; }
  .member-bio {
    margin-top: 20px; font-size: 14px; line-height: 25.5px; color: var(--body-text);
  }
  .member-social {
    list-style: none; display: flex; justify-content: center; align-items: center;
    gap: 18px; margin-top: 26px; height: 32px;
  }
  .member--right .member-social { margin-top: 17px; }
  .social-link { width: 14px; height: 14px; border-radius: 50%; background: var(--icon-grey); }
  .social-link--active { width: 31px; height: 31px; background: var(--accent); }

  .counter {
    position: absolute; left: 0; top: 770px; width: 1200px; height: 230px; background: var(--band-bg);
  }
  .counter-rule { position: absolute; left: 0; top: 25px; width: 1200px; height: 1px; background: var(--band-rule); }
  .counter .section-title { top: 96px; color: var(--white); }
</style>
</head>
<body>
  <section class="team">
    <h1 class="section-title">We Love Animals</h1>
    <div class="title-rule" style="left:500px; top:95px; width:196px; background:var(--rule);"></div>
    <div class="title-mark" role="img" aria-label="Small cat emblem" style="left:591px; top:77px; background:var(--ink);"></div>

    <svg class="connector" width="1200" height="34" viewBox="0 0 1200 34" aria-hidden="true">
      <g fill="var(--white)">
        <circle cx="168" cy="17" r="2.5"/><circle cx="183" cy="17" r="4.5"/><circle cx="198" cy="17" r="2.5"/>
        <circle cx="495" cy="17" r="2.5"/><circle cx="510" cy="17" r="4.5"/><circle cx="525" cy="17" r="2.5"/>
        <circle cx="540" cy="17" r="2.5"/><circle cx="555" cy="17" r="4.5"/><circle cx="571" cy="17" r="4.5"/>
        <circle cx="629" cy="17" r="4.5"/><circle cx="645" cy="17" r="2.5"/><circle cx="661" cy="17" r="4.5"/>
        <circle cx="676" cy="17" r="2.5"/><circle cx="691" cy="17" r="2.5"/><circle cx="706" cy="17" r="2.5"/>
        <circle cx="1000" cy="17" r="2.5"/><circle cx="1015" cy="17" r="4.5"/><circle cx="1030" cy="17" r="2.5"/>
      </g>
      <rect role="img" aria-label="Small cat emblem" x="588" y="8" width="24" height="20" rx="9" fill="var(--ink)"/>
    </svg>

    <article class="member member--left">
      <div class="portrait">
        <div class="portrait-fill portrait-fill--man" role="img" aria-label="Photo of a volunteer sitting on steps"></div>
      </div>
      <h2 class="member-name"><strong>Owen</strong> Hale</h2>
      <p class="member-bio">Lorem ipsum dolor sit amet, consectetur adipiscing<br>elit, sed do eiusmod tempor incididunt ut<br>abore et dolore magna aliqua.</p>
      <ul class="member-social" aria-label="Social links">
        <li class="social-link" aria-label="Social profile 1"></li>
        <li class="social-link" aria-label="Social profile 2"></li>
        <li class="social-link" aria-label="Social profile 3"></li>
        <li class="social-link" aria-label="Social profile 4"></li>
        <li class="social-link" aria-label="Social profile 5"></li>
      </ul>
    </article>

    <article class="member member--right">
      <div class="portrait">
        <div class="portrait-fill portrait-fill--woman" role="img" aria-label="Photo of a volunteer with a dog and a kitten"></div>
      </div>
      <h2 class="member-name"><strong>Nora</strong> Whitby</h2>
      <p class="member-bio">Lorem ipsum dolor sit amet, consectetur adipiscing<br>elit, sed do eiusmod tempor incididunt ut<br>labore et dolore magna aliqua.</p>
      <ul class="member-social" aria-label="Social links">
        <li class="social-link" aria-label="Social profile 1"></li>
        <li class="social-link" aria-label="Social profile 2"></li>
        <li class="social-link" aria-label="Social profile 3"></li>
        <li class="social-link social-link--active" aria-label="Social profile 4"></li>
        <li class="social-link" aria-label="Social profile 5"></li>
      </ul>
    </article>
  </section>

  <section class="counter">
    <div class="counter-rule"></div>
    <h2 class="section-title">Our Animals Counter</h2>
    <div class="title-rule" style="left:502px; top:178px; width:194px; background:var(--white);"></div>
    <div class="title-mark" role="img" aria-label="Small cat emblem" style="left:590px; top:158px; background:var(--white);"></div>
  </section>
</body>
</html>
```